Business card for law firm

Need business card for new law firm. Think confident, authoritative, conservative, but not stuffy or old-fashioned.

Contact Information for Business Card

Content for card - logo (uploaded), plus the following:

Paul Whitcombe (larger font)
Managing Partner (larger font, but not as large as name)
Level 9, 7 Ferris Lane
Sydney NSW 2000
Main Tel 02 9364 2710
Direct Tel 02 8472 3159
Email paul@qvlegal.com.au
www.qvlegal.com.au

Letterhead design should include logo plus:
Level 9, 7 Ferris Lane
Sydney NSW 2000
Tel 02 8472 3159
www.qvlegal.com.au

```html
<!DOCTYPE html>
<html lang="en">
<head>
<meta charset="UTF-8">
<title>Quayview Legal – Business Card</title>
<link href="https://fonts.googleapis.com/css2?family=Cinzel:wght@500&family=Montserrat:wght@400;500&display=swap" rel="stylesheet">
<style>
  :root {
    --backdrop: #1c1c1e;
    --card-navy: #252f78;
    --card-navy-deep: #1f2866;
    --mark-slate: #56618a;
    --text-silver: #c8ccd8;
    --text-soft: #aeb3c6;
    --rule: #8a90ab;
  }
  * { margin: 0; padding: 0; box-sizing: border-box; }
  html, body {
    width: 1200px;
    height: 900px;
    overflow: hidden;
    background: var(--backdrop);
  }
  .stage {
    position: relative;
    width: 1200px;
    height: 900px;
  }
  .card {
    position: absolute;
    left: 260px;
    width: 680px;
    height: 389px;
    background: linear-gradient(135deg, var(--card-navy) 0%, var(--card-navy-deep) 100%);
    border-radius: 3px;
  }
  .card--front { top: 45px; }
  .card--back { top: 466px; }

  .brand {
    display: flex;
    flex-direction: column;
    align-items: center;
    gap: 22px;
  }
  .brand__square {
    width: 58px;
    height: 58px;
    background: var(--mark-slate);
  }
  .brand__name {
    font-family: "Cinzel", serif;
    font-weight: 500;
    font-size: 34px;
    letter-spacing: 2px;
    color: var(--mark-slate);
    white-space: nowrap;
  }
  .card--front .brand {
    position: absolute;
    left: 0; right: 0;
    top: 118px;
  }
  .card--back .brand {
    position: absolute;
    left: 40px;
    width: 300px;
    top: 118px;
  }
  .card--back .brand__name { font-size: 30px; }

  .divider {
    position: absolute;
    left: 362px;
    top: 80px;
    width: 1px;
    height: 232px;
    background: var(--rule);
  }
  .details {
    position: absolute;
    left: 392px;
    top: 78px;
    font-family: "Montserrat", sans-serif;
    color: var(--text-silver);
  }
  .details__name {
    font-family: "Cinzel", serif;
    font-weight: 500;
    font-size: 23px;
    letter-spacing: 0.5px;
    line-height: 1.1;
  }
  .details__role {
    font-size: 15px;
    color: var(--text-soft);
    margin-top: 2px;
    letter-spacing: 0.4px;
  }
  .details__address {
    font-size: 15px;
    line-height: 1.35;
    margin-top: 14px;
    letter-spacing: 0.3px;
  }
  .contact-list {
    list-style: none;
    margin-top: 14px;
  }
  .contact-list li {
    display: flex;
    align-items: center;
    gap: 12px;
    font-size: 15px;
    line-height: 1.55;
    letter-spacing: 0.3px;
  }
  .contact-list svg {
    width: 14px;
    height: 14px;
    flex: none;
    stroke: var(--text-silver);
    fill: none;
    stroke-width: 1.6;
  }
</style>
</head>
<body>
<main class="stage">
  <section class="card card--front" aria-label="Card front">
    <div class="brand">
      <div class="brand__square"></div>
      <div class="brand__name">Quayview Legal</div>
    </div>
  </section>

  <section class="card card--back" aria-label="Card back">
    <div class="brand">
      <div class="brand__square"></div>
      <div class="brand__name">Quayview Legal</div>
    </div>
    <div class="divider"></div>
    <div class="details">
      <p class="details__name">PAUL WHITCOMBE</p>
      <p class="details__role">Managing Partner</p>
      <p class="details__address">Level 9, 7 Ferris Lane<br>Sydney NSW 2000</p>
      <ul class="contact-list">
        <li>
          <svg viewBox="0 0 16 16" aria-hidden="true"><path d="M3 2 L6 2 L7 5 L5.5 6.5 C6.5 8.5 7.5 9.5 9.5 10.5 L11 9 L14 10 L14 13 C8 13.5 2.5 8 3 2 Z"/></svg>
          02 9364 2710
        </li>
        <li>
          <svg viewBox="0 0 16 16" aria-hidden="true"><rect x="4" y="1.5" width="8" height="13" rx="1.5"/><line x1="7" y1="12" x2="9" y2="12"/></svg>
          02 8472 3159
        </li>
        <li>
          <svg viewBox="0 0 16 16" aria-hidden="true"><rect x="1.5" y="3.5" width="13" height="9" rx="1"/><polyline points="1.5,4 8,9 14.5,4"/></svg>
          paul@qvlegal.com.au
        </li>
        <li>
          <svg viewBox="0 0 16 16" aria-hidden="true"><circle cx="8" cy="8" r="6.5"/><ellipse cx="8" cy="8" rx="2.8" ry="6.5"/><line x1="1.5" y1="8" x2="14.5" y2="8"/></svg>
          www.qvlegal.com.au
        </li>
      </ul>
    </div>
  </section>
</main>
</body>
</html>
```